Podcast Art for Bright Belly Radio: Rising above Daily Flares

Read carefully Please. Most submittals so far have not read this.

We're looking for stunning, eye-catching, innovative yet simple podcast art for our first Podcast

Background should be solid, one color

Bright Belly Radio: Rising beyond Daily Flares
with Marcus Telford

Use our Brand Guide including logo, colors, and font
https://lnk.example-short.net/BBR2020StyleKit

Some Podcast Covers I like: https://casts.wavelane-audio.net/

Optional: Captain Flush graphic included above and/or my headshot uploaded below

As you can see humor / medutainment is part of the brand. As we are talking serious topic such as a disease many suffer from you can see the humor in the logo and "captain flush" . Here is the monologue for the first episode to give you a deeper feel on the content

https://files.papermoor-docs.net/doc/7qR_Lk2mWz9PdXc4VtBn8JhYs3FaEo6GuKwTn/edit?share=link

Target Market(s)

Those who suffer from gut issues, are diagnosed with inflammatory bowel disease(IBD), Crohn's Disease or Ulcerative Colitis - also their coaches, doctors, practitioners so functional or integrative medicine doctors/coaches, gastroenterologists etc.

Industry/Entity Type

Health And Wellness

Font styles to use
Other font styles liked:
• Primary: Oswald bold. Secondary: Oswald Medium or light

Requirements
Must have
• 3000 x 3000 pixels
Simple and eye-catching
Brand Guide Logo
Brand Guide Font
Brand Guide Colors including accent color(s)
I did not select colors below because I have included our Brand guide. Please use the exact colors there.
Nice to have
• Maybe my headshot and/or the captain flush graphic - if not too busy and still looks good
Should not have
• - Look busy
- Reverse Logo
- Not follow the Brand Guide
- Anything in the background but one solid color from the brief

```html
<!DOCTYPE html>
<html lang="en">
<head>
<meta charset="utf-8">
<title>Bright Belly Radio: Rising beyond Daily Flares</title>
<link href="https://fonts.googleapis.com/css2?family=Oswald:wght@500;700&display=swap" rel="stylesheet">
<style>
  :root {
    --brand-pink: #d93a82;
    --brand-navy: #233f74;
    --brand-sky: #c8e6f0;
    --brand-yellow: #f5e27b;
  }
  * { margin: 0; padding: 0; box-sizing: border-box; }
  html, body {
    width: 1200px;
    height: 1200px;
    overflow: hidden;
    background: var(--brand-navy);
  }
  .cover {
    position: relative;
    width: 1200px;
    height: 1200px;
    background: var(--brand-navy);
    font-family: "Oswald", sans-serif;
    overflow: hidden;
  }
  .divider-stripe {
    position: absolute;
    left: 426px;
    top: 0;
    width: 11px;
    height: 1200px;
    background: var(--brand-yellow);
  }
  .brand-name {
    position: absolute;
    left: 30px;
    top: 190px;
    width: 370px;
    text-align: center;
    color: var(--brand-pink);
    font-weight: 700;
    font-size: 92px;
    text-transform: uppercase;
    line-height: 1.18;
    letter-spacing: 1px;
  }
  .brand-name span { display: block; }
  .show-title {
    position: absolute;
    left: 516px;
    top: 70px;
    color: var(--brand-sky);
    font-weight: 700;
    line-height: 1;
  }
  .show-title span { display: block; }
  .title-lead {
    font-size: 178px;
    line-height: 0.95;
    text-transform: uppercase;
    letter-spacing: 1px;
  }
  .title-joiner {
    font-size: 86px;
    line-height: 1;
    margin-top: 4px;
    letter-spacing: 1px;
  }
  .title-main {
    font-size: 200px;
    line-height: 0.92;
    letter-spacing: -1px;
  }
  .host-credit {
    position: absolute;
    left: 522px;
    top: 905px;
    color: var(--brand-yellow);
    text-transform: uppercase;
    line-height: 1.05;
  }
  .host-credit span { display: block; }
  .host-credit .credit-label { font-weight: 700; font-size: 34px; letter-spacing: 2px; }
  .host-credit .host-first { font-weight: 700; font-size: 62px; letter-spacing: 3px; line-height: 1.05; }
  .host-credit .host-last { font-weight: 500; font-size: 44px; letter-spacing: 2px; }
  .host-portrait {
    position: absolute;
    left: 782px;
    top: 768px;
    width: 348px;
    height: 348px;
    border-radius: 50%;
    border: 7px solid var(--brand-pink);
    background: radial-gradient(circle at 50% 40%, #d9cfc4 0%, #b3a392 55%, #8c7d6e 100%);
  }
</style>
</head>
<body>
  <main class="cover">
    <div class="brand-name">
      <span>Bright</span>
      <span>Belly</span>
      <span>Radio</span>
    </div>
    <div class="divider-stripe"></div>

    <h1 class="show-title">
      <span class="title-lead">Rising</span>
      <span class="title-joiner">beyond</span>
      <span class="title-main">Daily</span>
      <span class="title-main">Flares</span>
    </h1>

    <p class="host-credit">
      <span class="credit-label">With</span>
      <span class="host-first">Marcus</span>
      <span class="host-last">Telford</span>
    </p>

    <div class="host-portrait" role="img" aria-label="Headshot of host Marcus Telford smiling, wearing a white shirt"></div>
  </main>
</body>
</html>
```